Banner Ad Design Project

We need a 728x90 and a 300x250
1st option
"I have a lead for you. Click here to close the deal."
In large bold letters.
Under this in smaller letters,
"Lornavel. For serious business networkers"
2nd option
"Put that coffee down!"
"Coffee's for closers only."
Close more deals. LORNAVEL LOGO
(this is a quote from Harrowmere Tide. It is a famous sales movie)
The other option is
"First you get the money" "Then you get the power" in bold letters.
"Lornavel. For serious business networkers" in smaller letters at the bottom.
-Must have our colors
-Must have our logo (Small at the bottom right)
-Watch the video at lornavel () com
Please be creative. If the banner can have multiple images that would be great as well.
This needs to be a serious looking ad that is bold and clean.
Updates
Please be sure to use the phrase, "Put that coffee down! Coffee's for closers only" with the logo and at the bottom the words, Lornavel, for serious business networkers. in one of the designs. This will be our first campaign. I am looking for a very simple design that is bold. Perhaps just a coffee cup with the words and no other graphics.
Target Market(s)
Sales professionals
Industry/Entity Type
Business
Look and feel

```html
<!DOCTYPE html>
<html lang="en">
<head>
<meta charset="utf-8">
<title>Lornavel Banner Set</title>
<link rel="stylesheet" href="https://fonts.googleapis.com/css2?family=Roboto+Condensed:wght@700&family=PT+Sans:wght@400;700&display=swap">
<style>
  :root {
    --stage: #3a3a3a;
    --stage-edge: #1e1e1e;
    --brand-blue: #2b4f9e;
    --brand-blue-deep: #1f3d82;
    --brand-green: #5bb431;
    --brand-orange: #f39a1e;
    --paper: #ffffff;
    --ink-light: #ffffff;
    --button-top: #ffe14a;
    --button-bottom: #f5aa00;
    --button-ink: #1a1a1a;
    --photo-light: #d9cfc6;
    --photo-dark: #2d2a2a;
  }
  * { margin: 0; padding: 0; box-sizing: border-box; }
  html, body { width: 1200px; height: 673px; overflow: hidden; }
  body {
    background: radial-gradient(ellipse at 45% 40%, var(--stage) 0%, var(--stage-edge) 100%);
    position: relative;
    font-family: "PT Sans", Arial, sans-serif;
  }
  .banner { position: absolute; overflow: hidden; background: var(--paper); }
  .banner-shape { position: absolute; inset: 0; width: 100%; height: 100%; }
  .photo {
    position: absolute; left: 0; top: 0; height: 100%;
    background: linear-gradient(170deg, var(--photo-light) 0%, #c8b3a3 55%, var(--photo-dark) 100%);
  }
  .brand { position: absolute; display: flex; align-items: center; gap: 8px; }
  .brand-mark { width: 32px; height: 32px; background: var(--brand-orange); border-radius: 6px; }
  .brand-name { font-family: "PT Sans", Arial, sans-serif; font-weight: 400; color: var(--brand-blue); line-height: 1; }
  .headline, .subline {
    position: absolute; color: var(--ink-light); text-align: center;
    font-family: "Roboto Condensed", "Arial Narrow", sans-serif; font-weight: 700;
    text-transform: uppercase; white-space: nowrap; line-height: 1.1;
    text-shadow: 0 1px 2px rgba(0,0,0,.35);
  }
  .tagline {
    position: absolute; color: var(--ink-light); text-align: center;
    font-family: "PT Sans", Arial, sans-serif; font-weight: 400; white-space: nowrap;
  }
  .cta {
    position: absolute; display: flex; align-items: center; justify-content: center; gap: 10px;
    background: linear-gradient(var(--button-top), var(--button-bottom));
    border-radius: 4px;
    font-family: "Roboto Condensed", "Arial Narrow", sans-serif; font-weight: 700;
    color: var(--button-ink); font-size: 19px; line-height: 1;
  }
  .cta-arrow { width: 24px; height: 24px; }

  /* medium rectangle 300x250 */
  .banner-rect { top: 88px; width: 424px; height: 353px; }
  .banner-rect.first { left: 131px; }
  .banner-rect.second { left: 585px; }
  .banner-rect .photo { width: 132px; }
  .banner-rect .brand { top: 32px; right: 26px; }
  .banner-rect .brand-name { font-size: 32px; }
  .banner-rect .headline { left: 138px; right: 8px; top: 160px; font-size: 25px; }
  .banner-rect .subline { left: 138px; right: 8px; top: 193px; font-size: 17px; }
  .banner-rect .tagline { left: 138px; right: 8px; top: 228px; font-size: 21px; line-height: 27px; }
  .banner-rect .cta { left: 207px; top: 312px; width: 180px; height: 36px; }

  /* leaderboard 728x90 */
  .banner-board { left: 71px; top: 480px; width: 1028px; height: 127px; }
  .banner-board .photo { width: 80px; }
  .banner-board .brand { left: 96px; top: 48px; }
  .banner-board .brand-name { font-size: 32px; }
  .banner-board .headline { left: 330px; right: 6px; top: 10px; font-size: 28px; }
  .banner-board .tagline { left: 330px; right: 6px; top: 48px; font-size: 24px; line-height: 28px; }
  .banner-board .cta { left: 587px; top: 86px; width: 177px; height: 36px; }
</style>
</head>
<body>
  <svg width="0" height="0" style="position:absolute">
    <defs>
      <linearGradient id="panel-blue" x1="0" y1="0" x2="1" y2="1">
        <stop offset="0" stop-color="#3560b0"/>
        <stop offset="1" stop-color="#1f3d82"/>
      </linearGradient>
      <symbol id="arrow-circle" viewBox="0 0 26 26">
        <circle cx="13" cy="13" r="12" fill="#222"/>
        <path d="M10 7 L16 13 L10 19" fill="none" stroke="#fff" stroke-width="3" stroke-linecap="round" stroke-linejoin="round"/>
      </symbol>
    </defs>
  </svg>

  <section class="banner banner-rect first">
    <svg class="banner-shape" viewBox="0 0 424 353" preserveAspectRatio="none">
      <path d="M132 104 Q270 178 424 100 L424 353 L132 353 Z" fill="url(#panel-blue)"/>
      <path d="M132 104 Q270 178 424 100" fill="none" stroke="var(--brand-green)" stroke-width="9"/>
    </svg>
    <div class="photo" role="img" aria-label="Photo of a smiling businesswoman in glasses and a dark suit"></div>
    <div class="brand"><span class="brand-mark"></span><span class="brand-name">Lornavel</span></div>
    <p class="headline">I have a lead for you</p>
    <p class="subline">Click here to close the deal</p>
    <p class="tagline">Lornavel. For serious<br>business networkers</p>
    <a class="cta">Learn More! <svg class="cta-arrow"><use href="#arrow-circle"/></svg></a>
  </section>

  <section class="banner banner-rect second">
    <svg class="banner-shape" viewBox="0 0 424 353" preserveAspectRatio="none">
      <path d="M132 104 Q270 178 424 100 L424 353 L132 353 Z" fill="url(#panel-blue)"/>
      <path d="M132 104 Q270 178 424 100" fill="none" stroke="var(--brand-green)" stroke-width="9"/>
    </svg>
    <div class="photo" role="img" aria-label="Photo of a smiling businesswoman in glasses and a dark suit"></div>
    <div class="brand"><span class="brand-mark"></span><span class="brand-name">Lornavel</span></div>
    <p class="headline">I have a lead for you</p>
    <p class="subline">Click here to close the deal</p>
    <p class="tagline">Lornavel. For serious<br>business networkers</p>
    <a class="cta">Learn More! <svg class="cta-arrow"><use href="#arrow-circle"/></svg></a>
  </section>

  <section class="banner banner-board">
    <svg class="banner-shape" viewBox="0 0 1028 127" preserveAspectRatio="none">
      <path d="M318 0 Q276 63 318 127 L1028 127 L1028 0 Z" fill="url(#panel-blue)"/>
      <path d="M318 0 Q276 63 318 127" fill="none" stroke="var(--brand-green)" stroke-width="9"/>
    </svg>
    <div class="photo" role="img" aria-label="Photo of a smiling businesswoman in glasses and a dark suit"></div>
    <div class="brand"><span class="brand-mark"></span><span class="brand-name">Lornavel</span></div>
    <p class="headline">I have a lead for you. Click here to close the deal</p>
    <p class="tagline">Lornavel. For serious business networkers</p>
    <a class="cta">Learn More! <svg class="cta-arrow"><use href="#arrow-circle"/></svg></a>
  </section>
</body>
</html>
```